Website for 3d printing & other services

Hi, i'm after a website to sell my 3d printed automotive parts as well as sell my 3d printing services & other services.

There's a few things i need the website to have:

- Automatic 3d print quoting based on the file the client uploads to the website.
- Shop function where i can sell my custom automotive parts
- 3D printing technologies offered are SLA & FDM
- My business can offer 3d printing, 3d scanning, 3d cad design, cnc machining, steel fabrication, drafting services.

The color design is to suit my logo which is Black, orange & white.

Target Market(s)

3d printing, automotive, fabrication

Industry/Entity Type

General manufacturing & Custom automotive parts

Coding

Coded - Design and coding required

Number of Pages Required

5+ page

Requirements
Must have
• Automatic 3d print quoting. Shop for my printed parts.

```html
<!DOCTYPE html>
<html lang="en">
<head>
<meta charset="utf-8">
<title>Korvan Works — 3D Printed Automotive Parts</title>
<link href="https://fonts.googleapis.com/css2?family=Mulish:wght@400;600;700;800;900&display=swap" rel="stylesheet">
<style>
:root{
  --orange:#ff6b00;
  --black:#000;
  --ink:#111;
  --white:#fff;
  --grey-bg:#f3f2f2;
  --line:#d6d6d6;
  --text:#333;
}
*{box-sizing:border-box;margin:0;padding:0}
html,body{width:1200px;height:4376px;overflow:hidden}
body{font-family:"Mulish",sans-serif;color:var(--text);background:var(--white);position:relative}
.abs{position:absolute}
.btn{position:absolute;background:var(--orange);color:var(--white);font-weight:800;text-transform:uppercase;display:flex;align-items:center;justify-content:center;letter-spacing:.5px}
.title{position:absolute;left:0;width:1200px;text-align:center;font-weight:900;font-size:34px;color:var(--ink);letter-spacing:.5px}
.rule{position:absolute;width:38px;height:3px;background:var(--orange);left:581px}

/* header */
.site-header{position:absolute;top:0;left:0;width:1200px;height:126px;background:var(--black)}
.brand{position:absolute;color:var(--orange);font-weight:900;white-space:nowrap;line-height:1}
.follow{position:absolute;left:555px;top:30px;color:var(--white);font-size:14px}
.social-sq{position:absolute;top:28px;width:22px;height:22px;border-radius:5px;background:var(--white)}
.call{position:absolute;left:802px;top:20px;color:var(--white)}
.call small{display:block;font-size:13px}
.call b{font-size:18px;font-weight:600}
.cart{position:absolute;left:1017px;top:28px;color:var(--white);font-size:11px;border-left:1px solid #777;padding-left:10px}
.cart b{display:block;font-size:15px;font-weight:600}
.badge{position:absolute;left:991px;top:28px;width:14px;height:14px;border-radius:50%;background:var(--orange);color:#fff;font-size:9px;text-align:center;line-height:14px}
.nav a{position:absolute;top:82px;color:var(--white);text-decoration:none;font-size:15px}
.nav a.active{color:var(--orange);font-weight:800;border-bottom:2px solid var(--orange);padding-bottom:6px}

/* hero */
.hero{position:absolute;top:126px;left:0;width:1200px;height:598px;background:radial-gradient(ellipse at 50% 40%,#9aa3a8,#5b6266 55%,#2f3538)}
.hero h1{position:absolute;top:155px;width:1200px;text-align:center;color:var(--white);font-weight:900;font-size:58px;line-height:70px;letter-spacing:1px;text-shadow:0 2px 8px rgba(0,0,0,.4)}
.dots{position:absolute;top:555px;left:568px;display:flex;gap:12px}
.dots i{width:9px;height:9px;border-radius:50%;background:#ddd}
.dots i.on{background:var(--orange)}

/* services */
.services{position:absolute;top:724px;left:0;width:1200px;height:888px;background:linear-gradient(#fff 60%,#f1f1f1)}
.svc-icon{position:absolute;width:92px;height:92px;border:1.5px solid #555;border-radius:50%;background:#fff;display:flex;align-items:center;justify-content:center}
.svc-card{position:absolute;width:279px;height:176px;border:1.5px solid var(--line);background:#fff}
.svc-card h3{position:absolute;top:-14px;left:0;width:100%;text-align:center}
.svc-card h3 span{background:#fff;padding:0 10px;font-size:21px;font-weight:800;color:var(--ink)}
.svc-card p{position:absolute;top:30px;left:30px;right:30px;text-align:center;font-size:12.5px;line-height:17px;color:#444}
.svc-card .btn{left:84px;bottom:-16px;width:108px;height:30px;font-size:12px}

/* about */
.about{position:absolute;top:1612px;left:0;width:1200px;height:491px;background:linear-gradient(90deg,#1a1a1a,#0b0b0b 60%,#151515)}
.about-photo{position:absolute;left:0;top:0;width:560px;height:491px;background:radial-gradient(circle at 45% 50%,#c8ced2,#7c868c 45%,#3a3f43 80%);clip-path:polygon(0 0,390px 0,420px 40px,470px 60px,500px 120px,540px 160px,520px 230px,555px 290px,520px 350px,490px 420px,440px 470px,400px 491px,0 491px)}
.about h2{position:absolute;left:612px;top:62px;color:#fff;font-size:33px;font-weight:900}
.about h2 em{font-style:normal;color:var(--orange)}
.about .sub{position:absolute;left:612px;top:104px;color:#fff;font-size:17px;letter-spacing:4px}
.about p{position:absolute;left:612px;top:175px;width:450px;color:#ddd;font-size:16px;line-height:25px}

/* products */
.products{position:absolute;top:2103px;left:0;width:1200px;height:682px;background:#fff}
.prod{position:absolute;top:168px;width:223px;height:391px;border:1.5px solid var(--line);text-align:center}
.prod .ph{position:absolute;left:20px;top:15px;width:181px;height:180px;border-radius:6px}
.prod h4{position:absolute;top:218px;width:100%;font-size:17px;font-weight:800;color:var(--ink)}
.prod p{position:absolute;top:248px;left:30px;right:30px;font-size:11px;line-height:15px;color:#555}
.prod .price{position:absolute;top:290px;width:100%;font-size:21px;font-weight:800;color:var(--ink)}
.prod .btn{left:50px;top:335px;width:121px;height:28px;font-size:12px}
.arrow{position:absolute;top:337px}
.view-all{position:absolute;left:515px;top:598px;width:168px;height:38px;border:1.5px solid var(--orange);color:var(--orange);font-weight:800;font-size:12px;display:flex;align-items:center;justify-content:center}

/* technologies */
.tech{position:absolute;top:2785px;left:0;width:1200px;height:632px;background:var(--grey-bg)}
.tech-photo{position:absolute;top:156px;width:462px;height:298px}
.tech-frame{position:absolute;top:402px;height:70px;border:3px solid var(--orange);border-bottom:none}
.tech-box{position:absolute;top:403px;width:430px;height:170px;background:var(--black);color:#fff}
.tech-box h3{position:absolute;left:26px;top:20px;font-size:23px;font-weight:800}
.tech-box p{position:absolute;left:26px;top:58px;width:385px;font-size:12.5px;line-height:17px}
.tech-box .btn{left:26px;top:114px;width:108px;height:32px;font-size:12px}

/* quote */
.quote{position:absolute;top:3417px;left:0;width:1200px;height:598px;background:radial-gradient(ellipse at 50% 60%,#2b2b2b,#121212 70%)}
.quote .title{color:#fff}
.field{position:absolute;background:#fff;font-size:12.5px;color:#222;font-weight:600;padding:14px 18px}

/* footer */
.site-footer{position:absolute;top:4015px;left:0;width:1200px;height:361px;background:var(--black);color:#fff}
.col h5{position:absolute;top:45px;font-size:13px;font-weight:800;padding-bottom:10px;border-bottom:1px solid #555;width:108px}
.info{position:absolute;font-size:11.5px;line-height:15px}
.dot{position:absolute;width:20px;height:20px;border-radius:50%;background:var(--orange);display:flex;align-items:center;justify-content:center}
.menu{position:absolute;left:750px;top:102px;font-size:11.5px;line-height:19px}
.foot-rule{position:absolute;left:129px;top:269px;width:933px;height:1px;background:#444}
.copy{position:absolute;top:311px;width:1200px;text-align:center;font-size:10.5px}
</style>
</head>
<body>

<header class="site-header">
  <div class="brand" style="left:130px;top:46px;font-size:26px">Korvan Works</div>
  <div class="follow">Follow us</div>
  <div class="social-sq" style="left:634px"></div>
  <div class="social-sq" style="left:668px"></div>
  <div class="social-sq" style="left:703px"></div>
  <svg class="abs" style="left:758px;top:22px" width="32" height="32" viewBox="0 0 24 24" fill="none" stroke="#fff" stroke-width="1.3"><path d="M5 3h4l2 5-2.5 1.5a11 11 0 0 0 6 6L16 13l5 2v4a2 2 0 0 1-2 2A16 16 0 0 1 3 5a2 2 0 0 1 2-2z"/></svg>
  <div class="call"><small>Call Us</small><b>+1 555 010 2040</b></div>
  <svg class="abs" style="left:975px;top:36px" width="22" height="22" viewBox="0 0 24 24" fill="none" stroke="#fff" stroke-width="1.6"><path d="M2 3h3l3 12h11l2-8H6"/><circle cx="9" cy="20" r="1.5"/><circle cx="18" cy="20" r="1.5"/></svg>
  <div class="badge">0</div>
  <div class="cart">My Cart<b>$0.00</b></div>
  <nav class="nav">
    <a class="active" style="left:469px">HOME</a>
    <a style="left:554px">ABOUT US</a>
    <a style="left:671px">SERVICES</a>
    <a style="left:782px">PRODUCTS</a>
    <a style="left:905px">BLOG</a>
    <a style="left:977px">CONTACT US</a>
  </nav>
</header>

<section class="hero" role="img" aria-label="Close-up photograph of grey 3D printed turbine blades">
  <h1>3D PRINTED<br>AUTOMOTIVE PARTS</h1>
  <div class="btn" style="left:522px;top:319px;width:155px;height:43px;font-size:18px">Shop Now</div>
  <div class="dots"><i></i><i class="on"></i><i></i><i></i></div>
</section>

<section class="services">
  <div class="rule" style="top:40px"></div>
  <h2 class="title" style="top:56px">OUR SERVICES</h2>
  <div class="rule" style="top:112px"></div>

  <div class="svc-icon" style="left:225px;top:162px"><svg width="46" height="46" viewBox="0 0 40 40" fill="none" stroke="#ff6b00" stroke-width="1.5"><path d="M6 6h28M12 6v6h16V6M17 12h6l-3 6z"/><path d="M12 26h16v8H12zM8 34h24"/></svg></div>
  <div class="svc-icon" style="left:555px;top:162px"><svg width="46" height="46" viewBox="0 0 40 40" fill="none" stroke="#ff6b00" stroke-width="1.5"><path d="M20 8l10 5v12l-10 5-10-5V13zM20 18l10-5M20 18L10 13M20 18v12"/><path d="M4 10V4h6M36 10V4h-6M4 30v6h6M36 30v6h-6"/></svg></div>
  <div class="svc-icon" style="left:881px;top:162px"><svg width="46" height="46" viewBox="0 0 40 40" fill="none" stroke="#ff6b00" stroke-width="1.5"><path d="M20 5l13 7v16l-13 7-13-7V12z"/><circle cx="20" cy="20" r="6"/><circle cx="20" cy="20" r="2.5"/></svg></div>

  <div class="svc-card" style="left:133px;top:291px"><h3><span>3d Printing</span></h3><p>Lorem ipsum dolor sit ame con secteturadipiscing elit, sed do eiusmod tempor incididunt ut labore et dolore magna aliqua. Ut enim ad minim veniam, quis nostrud exercitati.</p><div class="btn">Read More</div></div>
  <div class="svc-card" style="left:461px;top:291px"><h3><span>3d Scanning</span></h3><p>Lorem ipsum dolor sit ame con secteturadipiscing elit, sed do eiusmod tempor incididunt ut labore et dolore magna aliqua. Ut enim ad minim veniam, quis nostrud exercitati.</p><div class="btn">Read More</div></div>
  <div class="svc-card" style="left:787px;top:291px"><h3><span>3d Cad Design</span></h3><p>Lorem ipsum dolor sit ame con secteturadipiscing elit, sed do eiusmod tempor incididunt ut labore et dolore magna aliqua. Ut enim ad minim veniam, quis nostrud exercitati.</p><div class="btn">Read More</div></div>

  <div class="svc-icon" style="left:225px;top:517px"><svg width="46" height="46" viewBox="0 0 40 40" fill="none" stroke="#ff6b00" stroke-width="1.5"><path d="M6 6h28v5H6zM16 11h8v8h-8zM18 19h4l-2 7z"/><path d="M6 32h28"/></svg></div>
  <div class="svc-icon" style="left:555px;top:517px"><svg width="46" height="46" viewBox="0 0 40 40" fill="none" stroke="#ff6b00" stroke-width="1.5"><path d="M12 16a8 8 0 0 1 16 0zM10 16h20"/><path d="M12 34c0-6 4-9 8-9s8 3 8 9M6 34h28"/></svg></div>
  <div class="svc-icon" style="left:881px;top:517px"><svg width="46" height="46" viewBox="0 0 40 40" fill="none" stroke="#ff6b00" stroke-width="1.5"><path d="M8 8h24v24H8zM12 26l16-14M12 14h8M12 18h5"/></svg></div>

  <div class="svc-card" style="left:133px;top:645px"><h3><span>CNC Machining</span></h3><p>Lorem ipsum dolor sit ame con secteturadipiscing elit, sed do eiusmod tempor incididunt ut labore et dolore magna aliqua. Ut enim ad minim veniam, quis nostrud exercitati.</p><div class="btn">Read More</div></div>
  <div class="svc-card" style="left:461px;top:645px"><h3><span>Steel Fabrication</span></h3><p>Lorem ipsum dolor sit ame con secteturadipiscing elit, sed do eiusmod tempor incididunt ut labore et dolore magna aliqua. Ut enim ad minim veniam, quis nostrud exercitati.</p><div class="btn">Read More</div></div>
  <div class="svc-card" style="left:787px;top:645px"><h3><span>Drafting</span></h3><p>Lorem ipsum dolor sit ame con secteturadipiscing elit, sed do eiusmod tempor incididunt ut labore et dolore magna aliqua. Ut enim ad minim veniam, quis nostrud exercitati.</p><div class="btn">Read More</div></div>
</section>

<section class="about">
  <div class="about-photo" role="img" aria-label="Photograph of a metal 3D printed turbine impeller on a gear"></div>
  <div class="abs" style="left:612px;top:42px;width:38px;height:3px;background:var(--orange)"></div>
  <h2>ABOUT <em>KORVAN</em></h2>
  <div class="sub">PRINT &amp; FABRICATION</div>
  <p>Sed ut perspiciatis unde omnis iste natus error sit voluptatem accusantium doloremque laudantium, totam rem aperiam, eaque ipsa quae ab illo inventore veritatis et quasi architecto beatae vitae dicta sunt explicabo. Nemo enim ipsam voluptatem quia voluptas sit aspernatur aut odit aut fugit, sed quia consequuntur magni dolores eos qui ratione voluptatem sequi nesciunt. Neque porro quisquam est, qui dolorem ipsum quia dolo</p>
  <div class="btn" style="left:613px;top:405px;width:108px;height:30px;font-size:12px">Read More</div>
</section>

<section class="products">
  <div class="rule" style="top:50px"></div>
  <h2 class="title" style="top:65px">CUSTOM AUTOMOTIVE PARTS</h2>
  <div class="rule" style="top:119px"></div>
  <svg class="arrow" style="left:66px" width="22" height="40" viewBox="0 0 22 40" fill="none" stroke="#555" stroke-width="2"><path d="M18 2L3 20l15 18"/></svg>
  <svg class="arrow" style="left:1112px" width="22" height="40" viewBox="0 0 22 40" fill="none" stroke="#555" stroke-width="2"><path d="M4 2l15 18L4 38"/></svg>

  <div class="prod" style="left:133px"><div class="ph" role="img" aria-label="Photo of a black printed mounting bracket" style="background:radial-gradient(circle,#3a3a3a 20%,#fff 60%)"></div><h4>Lorem Ipsum</h4><p>Lorem ipsum dolor sit ame con sectetur adipiscing</p><div class="price">$25.99</div><div class="btn">Add to Cart</div></div>
  <div class="prod" style="left:371px"><div class="ph" role="img" aria-label="Photo of a grey printed camshaft part" style="background:radial-gradient(ellipse,#b8b8b8 20%,#fff 60%)"></div><h4>Lorem Ipsum</h4><p>Lorem ipsum dolor sit ame con sectetur adipiscing</p><div class="price">$25.99</div><div class="btn">Add to Cart</div></div>
  <div class="prod" style="left:610px"><div class="ph" role="img" aria-label="Photo of a finned printed engine cover" style="background:radial-gradient(ellipse,#5d5a5d 30%,#fff 65%)"></div><h4>Lorem Ipsum</h4><p>Lorem ipsum dolor sit ame con sectetur adipiscing</p><div class="price">$25.99</div><div class="btn">Add to Cart</div></div>
  <div class="prod" style="left:847px"><div class="ph" role="img" aria-label="Photo of grey and blue printed linkage parts" style="background:radial-gradient(ellipse,#8ea3c4 15%,#cfd3d8 40%,#fff 65%)"></div><h4>Lorem Ipsum</h4><p>Lorem ipsum dolor sit ame con sectetur adipiscing</p><div class="price">$25.99</div><div class="btn">Add to Cart</div></div>

  <div class="view-all">VIEW ALL PRODUCTS</div>
</section>

<section class="tech">
  <div class="rule" style="top:40px"></div>
  <h2 class="title" style="top:56px">3D PRINTING TECHNOLOGIES</h2>
  <div class="rule" style="top:112px"></div>

  <div class="tech-photo" role="img" aria-label="Photograph of an SLA resin printer with cream parts" style="left:133px;background:linear-gradient(135deg,#c7c3a8,#e8ddb4 45%,#6e6a5a)"></div>
  <div class="tech-photo" role="img" aria-label="Photograph of an FDM printer nozzle printing a white gear" style="left:607px;background:linear-gradient(160deg,#2a2d33,#4a4f58 50%,#3a4a78)"></div>

  <div class="tech-frame" style="left:133px;width:462px"></div>
  <div class="tech-frame" style="left:607px;width:462px"></div>

  <div class="tech-box" style="left:151px"><h3>SLA</h3><p>Lorem ipsum dolor sit ame con sectetur adipiscing elit, sed do eiusmod tempor incididunt ut labore et dolore magna aliqua. Ut enim ad minim veniam, quis nostrud</p><div class="btn">Read More</div></div>
  <div class="tech-box" style="left:626px"><h3>FDM</h3><p>Lorem ipsum dolor sit ame con sectetur adipiscing elit, sed do eiusmod tempor incididunt ut labore et dolore magna aliqua. Ut enim ad minim veniam, quis nostrud</p><div class="btn">Read More</div></div>
</section>

<section class="quote">
  <div class="rule" style="top:60px"></div>
  <h2 class="title" style="top:70px">GET A QUOTE</h2>
  <div class="rule" style="top:124px"></div>
  <div class="field" style="left:279px;top:167px;width:313px;height:42px">FIRST NAME</div>
  <div class="field" style="left:607px;top:167px;width:314px;height:42px">LAST NAME</div>
  <div class="field" style="left:279px;top:228px;width:313px;height:42px">EMAIL ID</div>
  <div class="field" style="left:607px;top:228px;width:314px;height:42px">PHONE</div>
  <div class="field" style="left:279px;top:289px;width:642px;height:46px">CHOOSE FILE</div>
  <div class="btn" style="left:816px;top:301px;width:98px;height:26px;font-size:14px">Upload</div>
  <div class="field" style="left:279px;top:352px;width:642px;height:124px">MESSAGE</div>
  <div class="btn" style="left:501px;top:510px;width:201px;height:46px;font-size:18px">Submit a Quote</div>
</section>

<footer class="site-footer">
  <div class="brand" style="left:138px;top:142px;font-size:38px">Korvan Works</div>

  <div class="col"><h5 style="left:449px">CONTACT US</h5></div>
  <div class="dot" style="left:449px;top:106px"><svg width="10" height="12" viewBox="0 0 10 12" fill="#fff"><path d="M5 0a4 4 0 0 1 4 4c0 3-4 8-4 8S1 7 1 4a4 4 0 0 1 4-4z"/></svg></div>
  <div class="info" style="left:481px;top:102px">214 Alder Lane, Unit 3<br>Riverton, CT 06065</div>
  <div class="dot" style="left:449px;top:158px"><svg width="11" height="11" viewBox="0 0 24 24" fill="#fff"><path d="M5 3h4l2 5-2.5 1.5a11 11 0 0 0 6 6L16 13l5 2v4a2 2 0 0 1-2 2A16 16 0 0 1 3 5a2 2 0 0 1 2-2z"/></svg></div>
  <div class="info" style="left:481px;top:154px">Call Us<br>+1 555 010 2040</div>
  <div class="dot" style="left:449px;top:209px"><svg width="11" height="9" viewBox="0 0 12 9" fill="none" stroke="#fff" stroke-width="1.3"><rect x=".7" y=".7" width="10.6" height="7.6"/><path d="M1 1l5 4 5-4"/></svg></div>
  <div class="info" style="left:481px;top:205px">E mail Us<br>info@korvanworks.example</div>

  <div class="col"><h5 style="left:750px">MENU</h5></div>
  <div class="menu">Home<br>About Us<br>Services<br>Products<br>Blog<br>Contact Us</div>

  <div class="col"><h5 style="left:959px">FOLLOW US</h5></div>
  <div class="dot" style="left:959px;top:112px"></div>
  <div class="info" style="left:994px;top:108px">Like us on<br>OUR PAGE</div>
  <div class="dot" style="left:959px;top:162px"></div>
  <div class="info" style="left:994px;top:158px">Follow us on<br>UPDATES</div>
  <div class="dot" style="left:959px;top:213px"></div>
  <div class="info" style="left:994px;top:209px">Follow us on<br>CLIPS</div>

  <div class="foot-rule"></div>
  <div class="copy">Copyright © 2023 All Rights Reserved</div>
</footer>

</body>
</html>
```